Business Card Design

We are a commercial real estate brokerage in San Francisco, leasing office buildings downtown.
I would like a clean, elegant look. Simple but powerful .

Industry/Entity Type

Business

Contact Information for Business Card

Derek Holloway
lic# 07258143
415.555.0172
derek@velt-commercial.example
velt-commercial.example

```html
<!DOCTYPE html>
<html lang="en">
<head>
<meta charset="utf-8">
<title>Velt Commercial — Business Card</title>
<link rel="stylesheet" href="https://fonts.googleapis.com/css2?family=Roboto:wght@400;500;700&display=swap">
<style>
  :root {
    --backdrop: #e9e9e9;
    --card: #ffffff;
    --slate: #6f7f98;
    --slate-text: #7d8ba1;
    --icon: #a3a9b3;
  }
  * { margin: 0; padding: 0; box-sizing: border-box; }
  html, body {
    width: 1200px;
    height: 695px;
    overflow: hidden;
    background: var(--backdrop);
    font-family: "Roboto", Arial, sans-serif;
  }
  .business-card {
    position: absolute;
    left: 10px;
    top: 0;
    width: 1180px;
    height: 695px;
    background: var(--card);
  }
  .brand {
    position: absolute;
    left: 86px;
    top: 108px;
    display: flex;
    align-items: center;
    gap: 40px;
  }
  .brand-square {
    width: 150px;
    height: 150px;
    background: var(--slate);
    opacity: 0.25;
  }
  .brand-name {
    color: var(--slate);
    font-weight: 500;
    line-height: 1;
    text-transform: uppercase;
  }
  .brand-name .primary { display: block; font-size: 104px; letter-spacing: 2px; }
  .brand-name .secondary { display: block; font-size: 42px; margin-top: 6px; letter-spacing: 1px; }
  .contact {
    position: absolute;
    left: 306px;
    top: 366px;
    color: var(--slate-text);
  }
  .contact-name {
    font-size: 36px;
    font-weight: 700;
    text-transform: uppercase;
    color: var(--slate);
    line-height: 44px;
  }
  .contact-licence {
    font-size: 31px;
    margin-top: 14px;
    line-height: 40px;
  }
  .contact-list { list-style: none; }
  .contact-list li {
    display: flex;
    align-items: center;
    gap: 16px;
    font-size: 30px;
    height: 59px;
    padding-left: 6px;
  }
  .contact-list li:first-child { height: 54px; }
  .contact-icon { width: 18px; height: 18px; flex: none; }
</style>
</head>
<body>
  <main class="business-card">
    <div class="brand">
      <div class="brand-square"></div>
      <div class="brand-name">
        <span class="primary">Velt</span>
        <span class="secondary">Commercial</span>
      </div>
    </div>

    <section class="contact">
      <h1 class="contact-name">Derek Holloway</h1>
      <p class="contact-licence">lic# 07258143</p>
      <ul class="contact-list">
        <li>
          <svg class="contact-icon" viewBox="0 0 18 18" aria-hidden="true"><circle cx="9" cy="9" r="8" fill="var(--icon)"/><path d="M6 5l2 2-1 1.5c.8 1.3 1.7 2.2 3 3L11.5 10l2 2-1.3 1.5C8.5 13 5 9.5 4.5 5.8z" fill="#fff"/></svg>
          415.555.0172
        </li>
        <li>
          <svg class="contact-icon" viewBox="0 0 18 18" aria-hidden="true"><circle cx="9" cy="9" r="8" fill="var(--icon)"/><rect x="4.5" y="6" width="9" height="6.5" fill="none" stroke="#fff" stroke-width="1.2"/><path d="M4.5 6l4.5 3.5L13.5 6" fill="none" stroke="#fff" stroke-width="1.2"/></svg>
          derek@velt-commercial.example
        </li>
        <li>
          <svg class="contact-icon" viewBox="0 0 18 18" aria-hidden="true"><circle cx="9" cy="9" r="7.5" fill="none" stroke="var(--icon)" stroke-width="1.5"/><ellipse cx="9" cy="9" rx="3" ry="7.5" fill="none" stroke="var(--icon)" stroke-width="1.2"/><path d="M1.5 9h15" stroke="var(--icon)" stroke-width="1.2"/></svg>
          velt-commercial.example
        </li>
      </ul>
    </section>
  </main>
</body>
</html>
```